Quillmarsh Property Solutions need a business card design

Hello guys. We would need a business card design asap please.
We are a start up property investment business based in London UK specialised in buying, selling, managing and letting properties and helping distressed property owners.
The name of our Business is Quillmarsh, the logo symbolises the four fundamental elements of the world (earth, air, fire and water) and so it stands for strength, stability, longevity.
We would like the business card to communicate professionalism and reliability. Many many thanks indeed for your work.

Details:

1.) Rosalind Updike
Property Investor
Mobile: +44(0)7700123456
Email: rosalind.quillmarsh@mailbox-example.com

2.) Dominic Updike
Property Investor
Mobile: +44(0)7700987654
Email: dominic.quillmarsh@mailbox-example.com

```html
<!DOCTYPE html>
<html lang="en">
<head>
<meta charset="utf-8">
<title>Quillmarsh Property Solutions – Business Card</title>
<link rel="stylesheet" href="https://fonts.googleapis.com/css2?family=Open+Sans:wght@400;600;700&family=Montserrat:wght@800&display=swap">
<style>
  :root {
    --bg: #e9eaee;
    --card-white: #ffffff;
    --brand-green: #0c5a2c;
    --accent-red: #c8202e;
    --accent-blue: #2a4fa8;
    --ink: #1a1a1a;
    --ink-soft: #444a50;
    --icon-blue: #4a78c6;
    --divider: #9aa0a6;
  }
  * { box-sizing: border-box; margin: 0; padding: 0; }
  html, body { width: 1200px; height: 987px; overflow: hidden; background: var(--bg); }
  body { position: relative; font-family: "Open Sans", Arial, sans-serif; }

  .card {
    position: absolute;
    width: 720px;
    height: 412px;
    left: 240px;
    border-radius: 30px;
    overflow: hidden;
    box-shadow: 0 10px 28px rgba(0,0,0,0.18);
  }
  .card--front { top: 46px; background: var(--card-white); }
  .card--back  { top: 528px; background: var(--brand-green); }

  .card__swoosh { position: absolute; inset: 0; width: 100%; height: 100%; }

  .brand {
    position: absolute;
    left: 60px;
    top: 120px;
    width: 280px;
  }
  .brand__mark {
    display: flex;
    align-items: center;
    gap: 12px;
  }
  .brand__square { width: 26px; height: 26px; background: var(--brand-green); }
  .brand__name {
    font-family: "Montserrat", Arial, sans-serif;
    font-weight: 800;
    font-size: 34px;
    letter-spacing: 0.5px;
    color: var(--ink);
  }
  .brand__tagline {
    margin-top: 4px;
    margin-left: 40px;
    font-family: "Montserrat", Arial, sans-serif;
    font-weight: 800;
    font-size: 12.5px;
    letter-spacing: 0.6px;
    color: var(--ink);
  }

  .divider {
    position: absolute;
    left: 358px;
    top: 96px;
    width: 2px;
    height: 110px;
    background: linear-gradient(to bottom, transparent, var(--divider), transparent);
  }

  .contact {
    position: absolute;
    left: 385px;
    top: 112px;
    list-style: none;
  }
  .contact__item {
    display: flex;
    align-items: center;
    gap: 10px;
    font-size: 19px;
    color: var(--ink-soft);
    margin-bottom: 22px;
  }
  .contact__icon { width: 18px; height: 18px; flex: none; }

  .holder {
    position: absolute;
    right: 44px;
    bottom: 30px;
    text-align: right;
    color: var(--card-white);
  }
  .holder__name { font-weight: 700; font-size: 27px; line-height: 1.15; }
  .holder__role { font-weight: 400; font-size: 21px; line-height: 1.2; }

  .back-brand {
    position: absolute;
    inset: 0;
    display: flex;
    align-items: center;
    justify-content: center;
    gap: 18px;
  }
  .back-brand__square { width: 40px; height: 40px; background: var(--card-white); }
  .back-brand__name {
    font-family: "Montserrat", Arial, sans-serif;
    font-weight: 800;
    font-size: 56px;
    color: var(--card-white);
    letter-spacing: 1px;
  }
</style>
</head>
<body>

<section class="card card--front" aria-label="Business card front">
  <svg class="card__swoosh" viewBox="0 0 720 412" preserveAspectRatio="none" aria-hidden="true">
    <path d="M0 262 C 150 290, 250 380, 420 350 C 560 325, 650 300, 720 330 L720 412 L0 412 Z" fill="var(--brand-green)"/>
    <path d="M0 236 C 150 262, 260 352, 430 330 C 560 312, 650 290, 720 312" fill="none" stroke="var(--accent-red)" stroke-width="3"/>
    <path d="M0 247 C 150 274, 260 364, 428 341 C 560 322, 650 298, 720 320" fill="none" stroke="var(--accent-blue)" stroke-width="2.5"/>
    <path d="M0 256 C 150 282, 255 372, 424 346 C 560 323, 650 296, 720 325" fill="none" stroke="var(--card-white)" stroke-width="3"/>
  </svg>

  <div class="brand">
    <div class="brand__mark">
      <span class="brand__square"></span>
      <span class="brand__name">QUILLMARSH</span>
    </div>
    <div class="brand__tagline">PROPERTY SOLUTIONS</div>
  </div>

  <div class="divider"></div>

  <ul class="contact">
    <li class="contact__item">
      <svg class="contact__icon" viewBox="0 0 18 18" aria-hidden="true">
        <rect x="4" y="1" width="10" height="16" rx="2" fill="var(--icon-blue)"/>
        <rect x="6" y="3" width="6" height="7" fill="#fff"/>
        <circle cx="9" cy="13.5" r="1.3" fill="#fff"/>
      </svg>
      <span>+44(0)7700987654</span>
    </li>
    <li class="contact__item">
      <svg class="contact__icon" viewBox="0 0 18 18" aria-hidden="true">
        <rect x="1" y="4" width="16" height="11" rx="1.5" fill="var(--icon-blue)"/>
        <path d="M1.5 5 L9 10.5 L16.5 5" fill="none" stroke="#fff" stroke-width="1.4"/>
      </svg>
      <span>dominic.quillmarsh@mailbox-example.com</span>
    </li>
  </ul>

  <div class="holder">
    <div class="holder__name">Dominic Updike</div>
    <div class="holder__role">Property Investor</div>
  </div>
</section>

<section class="card card--back" aria-label="Business card back">
  <div class="back-brand">
    <span class="back-brand__square"></span>
    <span class="back-brand__name">QUILLMARSH</span>
  </div>
</section>

</body>
</html>
```